Start-Up für Training, Coaching & Consulting sucht modernes Webdesign!
Zielgruppe
Wer ist TAVI Training, Coaching & Consulting?
Wir führen Führungskräftetrainings durch, machen Privatkunden für Bewerbungen fit und unterstützen Unternehmen mit Verkaufstrainings. Wir entwickeln Persönlichkeiten im Coaching. Wir beraten Unternehmen und helfen ihnen dabei, ihre Geschäftsabläufe und Prozesse zu optimieren. Dabei steht unsere hohe Qualität im Mittelpunkt - gemeinsam mit unseren kreativen Trainingsmethoden. Unser Background (Diplom-Kaufleute und geprüfte Trainer) bietet dafür die passende Ausgangslage.
Was bedeutet TAVI?
Tavi ist Maori und bdeutet Kreis/Spirale. Er symbolisiert einen wachsenden Silberfarn und steht für persönliche Entwicklung und Entfaltung. Der Tavi ist einerseits unser Namensgeber und unser Logo, andererseits steht der Tavi aber auch für unsere Werte: Denn wir wollen unseren Kunden dabei helfen zu wachsen und sich weiterzuentwickeln - und dies auf eine hochqualitative und seriöse Art und Weise ohne den Eindruck von Esoterik oder Erlebnispädagogik zu vermitteln.
Aufgabenstellung
Modernes Design, das unsere Philosophie widerspiegelt: Wir möchten unseren Kunden auf seriöse und hochqualitative Weise weiterentwickeln. Wir stehen für nachhaltigen Lernerfolg, kreative Trainingsmethoden, Abwechslung, Spaß am Lernen, Qualität, Kompetenz, Fachwissen und Dynamik.
Layout:
1) Header: QMSR geprüfter Trainer, Menüpunkte (siehe Architektur)
2) Banner
3) 3 Teaser (Training, Coaching, Consulting) + Header + 2-3 Zeilen Text (+Icons)
>>> Sichtbarer Bereich auf Homepage: Menü, Banner, Teaser
4) "Warum Sie uns wählen sollten": 5 bullet points ohne weiteren Text
5) "Aus unserem Blog": Frame für 3 Blogartikel + Bild + Datum + Header + 2-3 Zeilen Text
6) Alle drei QMSR Logos
7) Footer: Click Us (quick links), Contact Us (Adresse), Follow Us (Pinnwald, ZOLP, Kontaktor)
8) Copyright + Impressum
>>> Das Design soll klar sein, aber nicht zu kantig. Vielmehr sollen abgerundete Ecken und dynamische Elemente genutzt werden.
Architektur:
3 Ebenen:
1) Homepage
2) TAVI, Training, Coaching, Consulting, für Trainer, Kundenstimmen/Referenzen, Kontakt
3) noch zu bestimmende Produktdetailseiten
Texte werden noch erstellt, Layout kann ggf. mit Platzhaltertext gefüllt werden.
Bildmaterial: Logo und vorhandenes Imagebild werden zur Verfügung gestellt. Bilder können ggf. gekauft werden. Vorschläge erwünscht.
Corporate colors:
grün: #a2c61b + monochromatic colors
http://www.tintoskop.de/a2c61b
grau: #474747 + monochromatic colors
http://www.tintoskop.de/474747

```html
<!DOCTYPE html>
<html lang="en">
<head>
<meta charset="utf-8">
<title>TAVI Training, Coaching & Consulting</title>
<link href="https://fonts.googleapis.com/css2?family=Jost:wght@400;500;600;700&display=swap" rel="stylesheet">
<style>
:root{
  --green:#a2c61b;
  --green-dark:#86a612;
  --grey:#474747;
  --ink:#2b2b2b;
  --text:#555;
  --light:#e6e6e6;
  --footer:#2a2a2a;
  --white:#fff;
}
*{margin:0;padding:0;box-sizing:border-box}
html,body{width:771px;height:1200px;overflow:hidden;background:var(--white)}
body{font-family:"Jost",sans-serif;color:var(--ink);position:relative}
.abs{position:absolute}
/* header */
.brand{left:152px;top:8px}
.brand-name{font-size:40px;font-weight:700;color:var(--grey);letter-spacing:1px;line-height:44px;display:flex;align-items:center;gap:6px}
.brand-name .dot{width:14px;height:14px;border-radius:50%;background:var(--green)}
.brand-tag{font-size:8px;color:var(--grey);border-top:1px solid var(--green);margin-top:5px;padding-top:2px;width:116px}
.brand-tag b{color:var(--green);font-weight:400}
.badges{top:5px;left:403px;display:flex;gap:26px}
.badge{background:#1f6fc1;height:26px}
.nav{top:51px;left:310px;display:flex;gap:8px;font-size:8.5px}
.nav span{padding:4px 11px;border-radius:10px;color:var(--ink)}
.nav .on{background:var(--green);color:var(--white)}
/* hero */
.hero{left:0;top:75px;width:771px;height:280px;background:radial-gradient(circle at 50% 45%,#6f9a3a 0%,#3c6a22 45%,#1f3d12 100%)}
.hero h1{position:absolute;top:78px;width:100%;text-align:center;color:var(--white);font-size:27px;font-weight:700;letter-spacing:.3px}
.hero h1 i{color:var(--green);font-style:normal}
.hero p{position:absolute;top:117px;left:180px;width:411px;text-align:center;color:var(--white);font-size:8px;line-height:15px}
.cta{position:absolute;top:163px;left:322px;width:127px;height:23px;border-radius:12px;background:var(--green);box-shadow:0 2px 0 var(--green-dark);color:var(--white);font-size:8.5px;font-weight:600;text-align:center;line-height:23px}
.arrow{position:absolute;top:107px;width:29px;height:29px;border-radius:50%;background:rgba(0,0,0,.25);color:var(--white);font-size:10px;text-align:center;line-height:29px}
.wave{left:0;top:310px}
/* what we do */
.section-title{top:362px;width:771px;text-align:center;font-size:20px;font-weight:700}
.section-title span{color:var(--green)}
.card{top:403px;width:143px;text-align:center}
.card .frame{height:90px;border:1px solid #ddd;padding:4px}
.card .photo{height:82px}
.card .icon{width:33px;height:33px;border-radius:50%;border:1.5px solid var(--green);background:var(--white);margin:-18px auto 0;position:relative;display:flex;align-items:center;justify-content:center}
.card h3{margin-top:10px;color:var(--green);font-size:10px;font-weight:500}
.card p{margin-top:9px;font-size:6.6px;line-height:12px;color:var(--text);padding:0 8px}
.btn{display:inline-block;margin-top:12px;border:1px solid #888;font-size:5.5px;font-weight:600;padding:3px 7px}
/* dark band */
.why{left:0;top:643px;width:386px;height:233px;background:linear-gradient(90deg,#1e2328,#2f3338 60%,#23262a)}
.blog{left:386px;top:643px;width:385px;height:233px;background:linear-gradient(90deg,#2b2c2a,#3b3a34 55%,#222)}
.notch{left:370px;top:643px}
.dark-h{font-size:17px;font-weight:700;line-height:21px;color:var(--white)}
.dark-h span{color:var(--green)}
.rule{height:1px;background:#666;width:170px;margin-top:9px}
.list{list-style:none;margin-top:13px}
.list li{font-size:7.5px;color:var(--white);display:flex;align-items:center;gap:10px;height:21px}
.list li:before{content:"›";width:8px;height:8px;border:1px solid #bbb;border-radius:50%;font-size:6px;line-height:6px;text-align:center;color:#ddd}
.btn-light{display:inline-block;border:1px solid #ccc;color:var(--white);font-size:5.5px;font-weight:600;padding:3px 7px}
.post{display:flex;gap:8px;margin-top:11px}
.thumb{width:56px;height:35px;border:1.5px solid #ddd;flex:none}
.post small{font-size:6px;color:#ddd;display:block}
.post h4{font-size:7.5px;font-weight:500;color:var(--green);margin-top:1px}
.post p{font-size:5.8px;color:#eee;line-height:10px;margin-top:4px}
/* partners */
.partners{left:0;top:876px;width:771px;height:150px;background:var(--light)}
.plogo{position:absolute;background:#1f6fc1}
/* footer */
.footer{left:0;top:1010px;width:771px;height:162px}
.fcol{top:1067px;color:var(--white)}
.fcol h5{font-size:8.5px;font-weight:600;letter-spacing:.2px}
.links{display:grid;grid-template-columns:56px 90px;row-gap:9px;margin-top:14px;font-size:7px}
.social{display:flex;gap:8px;margin-top:14px;font-size:6.5px;align-items:center}
.social span{display:flex;align-items:center;gap:3px}
.social i{width:9px;height:9px;background:var(--green);border-radius:2px}
.contact{margin-top:12px;font-size:7px;line-height:9px}
.contact div{display:flex;gap:9px;margin-bottom:9px}
.contact svg{flex:none;margin-top:1px}
.copy{left:0;top:1172px;width:771px;height:28px;background:var(--green);color:var(--white);font-size:7px;text-align:center;line-height:28px}
</style>
</head>
<body>

<header>
  <div class="abs brand">
    <div class="brand-name"><span>TAVI</span><i class="dot"></i></div>
    <div class="brand-tag">Training <b>•</b> Coaching <b>•</b> Consulting</div>
  </div>
  <div class="abs badges" aria-label="Partner badges">
    <div class="badge" style="width:22px"></div>
    <div class="badge" style="width:22px;margin-left:20px"></div>
    <div class="badge" style="width:60px;height:16px;margin-top:4px;margin-left:38px"></div>
  </div>
  <nav class="abs nav">
    <span>Home</span><span class="on">Training</span><span>Coaching</span><span>Consulting</span><span>Products</span><span>Contact</span>
  </nav>
</header>

<section class="abs hero" role="img" aria-label="Close-up of an unfurling green fern frond">
  <h1>TRAINING <i>•</i> COACHING <i>•</i> CONSULTING</h1>
  <p>Lorem ipsum dolor sit amet, consectetur adipisicing elit, sed do eiusmod tempor incididunt ut labore et dolore magna aliqua. Ut enim ad minim veniam,</p>
  <div class="cta">GET CONTACT US NOW</div>
  <div class="arrow" style="left:61px">‹</div>
  <div class="arrow" style="left:680px;color:var(--green)">›</div>
</section>
<svg class="abs wave" width="771" height="50" viewBox="0 0 771 50">
  <path d="M0 20 C150 2 260 8 400 28 C540 46 660 42 771 24 L771 50 L0 50Z" fill="var(--white)"/>
  <path d="M0 20 C150 2 260 8 400 28 C540 46 660 42 771 24" fill="none" stroke="var(--green)" stroke-width="3"/>
</svg>

<h2 class="abs section-title">WHAT <span>WE DO</span></h2>

<article class="abs card" style="left:152px">
  <div class="frame"><div class="photo" role="img" aria-label="Trainer presenting to a meeting group" style="background:linear-gradient(135deg,#c9ced6,#5677b8)"></div></div>
  <div class="icon"><svg width="14" height="14" viewBox="0 0 14 14" fill="none" stroke="#777"><rect x="6" y="1" width="7" height="5"/><circle cx="3" cy="4" r="1.5"/><path d="M1 13V7h4v6M7 13V9M11 13V9"/></svg></div>
  <h3>TRAINING</h3>
  <p>This is Photoshop's version of Lorem Ipsum. Proin gravida nibh vel velit auctor aliquet.</p>
  <span class="btn">READ MORE</span>
</article>
<article class="abs card" style="left:314px">
  <div class="frame"><div class="photo" role="img" aria-label="Hand drawing a rising arrow beside a glowing figure" style="background:linear-gradient(135deg,#0d2a33,#1a3e4a 50%,#2c3a40)"></div></div>
  <div class="icon"><svg width="14" height="12" viewBox="0 0 14 12" fill="var(--green)"><circle cx="7" cy="3" r="2"/><circle cx="3" cy="5" r="1.6"/><circle cx="11" cy="5" r="1.6"/><path d="M4 11a3 3 0 016 0z M0 11a2.5 2.5 0 014 -1v1z M14 11a2.5 2.5 0 00-4-1v1z"/></svg></div>
  <h3>COACHING</h3>
  <p>This is Photoshop's version of Lorem Ipsum. Proin gravida nibh vel velit auctor aliquet.</p>
  <span class="btn">READ MORE</span>
</article>
<article class="abs card" style="left:476px">
  <div class="frame"><div class="photo" role="img" aria-label="Two consultants talking at a desk" style="background:linear-gradient(135deg,#dfe3e8,#6a7c95 60%,#2a3a5a)"></div></div>
  <div class="icon"><svg width="14" height="12" viewBox="0 0 14 12" fill="#777"><circle cx="5" cy="3" r="2"/><path d="M1 11a4 4 0 018 0z"/><rect x="8" y="1" width="5" height="4" rx="1" fill="var(--green)"/></svg></div>
  <h3>CONSULTING</h3>
  <p>This is Photoshop's version of Lorem Ipsum. Proin gravida nibh vel velit auctor aliquet.</p>
  <span class="btn">READ MORE</span>
</article>

<section class="abs why" role="img" aria-label="Business people shaking hands in a dark office">
  <div style="position:absolute;left:152px;top:30px">
    <h2 class="dark-h">WHY SHOULD<br><span>CHOOS US</span></h2>
    <div class="rule"></div>
    <ul class="list">
      <li>Lorem ipsum dolor sit amet, consectetur adipisicing elit</li>
      <li>Sed do eiusmod tempor incididunt ut labore et dolore</li>
      <li>magna aliqua. Ut enim ad minim veniam,</li>
      <li>Quis nostrud exercitation ullamco laboris nisi ut</li>
      <li>Aliquip ex ea commodo consequat.</li>
    </ul>
    <span class="btn-light" style="margin-top:11px">READ MORE</span>
  </div>
</section>
<section class="abs blog" role="img" aria-label="Businessman standing on a road at dusk">
  <div style="position:absolute;left:29px;top:30px;width:210px">
    <h2 class="dark-h">LATEST NEWS FROM<br><span>OUR BLOG</span></h2>
    <div class="rule"></div>
    <div class="post">
      <div class="thumb" role="img" aria-label="Hand pointing at a growth chart" style="background:linear-gradient(135deg,#1f3a45,#4c6f6a)"></div>
      <div><small>16/12/2015</small><h4>Lorem ipsum dolor sit amet, consectetur</h4><p>Tempor incididunt ut labore et dolore magna aliqua. Ut enim ad minim veniam</p></div>
    </div>
    <div class="post" style="margin-top:14px">
      <div class="thumb" role="img" aria-label="Business team shaking hands" style="background:linear-gradient(135deg,#dfe6ef,#41597e)"></div>
      <div><small>16/12/2015</small><h4>Lorem ipsum dolor sit amet, consectetur</h4><p>Tempor incididunt ut labore et dolore magna aliqua. Ut enim ad minim veniam</p></div>
    </div>
    <span class="btn-light" style="margin:13px 0 0 5px">READ MORE</span>
  </div>
</section>
<svg class="abs notch" width="32" height="12" viewBox="0 0 32 12"><path d="M0 0L16 12L32 0Z" fill="var(--white)"/></svg>

<section class="abs partners" aria-label="Association badges">
  <div class="plogo" style="left:166px;top:42px;width:42px;height:56px"></div>
  <div class="plogo" style="left:316px;top:42px;width:43px;height:56px"></div>
  <div class="plogo" style="left:483px;top:52px;width:124px;height:32px"></div>
</section>

<svg class="abs footer" width="771" height="162" viewBox="0 0 771 162">
  <path d="M0 18 C150 4 280 8 420 24 C560 40 670 40 771 22 L771 162 L0 162Z" fill="var(--footer)"/>
  <path d="M0 18 C150 4 280 8 420 24 C560 40 670 40 771 22" fill="none" stroke="var(--green)" stroke-width="3"/>
</svg>

<div class="abs fcol" style="left:152px">
  <h5>QUICK LINKS</h5>
  <div class="links"><span>Home</span><span>Products</span><span>Training</span><span>Fr Trainer</span><span>Coaching</span><span>Customer Testimonials</span><span>Consulting</span><span>Contact</span></div>
</div>
<div class="abs fcol" style="left:341px">
  <h5>FOLLOW US</h5>
  <div class="social"><span><i></i>Pinnwald</span><span><i></i>ZOLP</span><span><i></i>Kontaktor</span></div>
</div>
<div class="abs fcol" style="left:483px">
  <h5>CONTACT US</h5>
  <div class="contact">
    <div><svg width="7" height="9" viewBox="0 0 7 9"><path d="M3.5 0a3 3 0 013 3c0 2-3 6-3 6S.5 5 .5 3a3 3 0 013-3z" fill="#fff"/><circle cx="3.5" cy="3" r="1" fill="var(--footer)"/></svg><span>#402, 1180 Maple Crescent<br>Fairview, BC V7K 2L9</span></div>
    <div><svg width="7" height="7" viewBox="0 0 7 7"><path d="M1 0l1.5 1.5-1 1a4 4 0 003 3l1-1L7 6 6 7C3 7 0 4 0 1z" fill="#fff"/></svg><span>555.210.4418 FREE</span></div>
    <div><svg width="7" height="6" viewBox="0 0 7 6"><rect width="7" height="6" fill="#fff"/><path d="M0 0l3.5 3L7 0" stroke="var(--footer)" fill="none"/></svg><span>info@tavi-training.com</span></div>
  </div>
</div>

<footer class="abs copy">Tavi © 2015 | All Rights Reserved</footer>
</body>
</html>
```